KPL Construction we build lodges in Botswana

We need a Design Layout only with Categories where we can update each projects photos.... We have a web address and a host - kpl.construction

```html
<!DOCTYPE html>
<html lang="en">
<head>
<meta charset="utf-8">
<title>KPL Construction</title>
<link href="https://fonts.googleapis.com/css2?family=Poppins:wght@500;600;700;800&family=Open+Sans:wght@400;600;700&display=swap" rel="stylesheet">
<style>
:root{
  --accent:#e8452c;
  --navy:#0f2b5b;
  --ink:#1d1d1d;
  --body:#555;
  --muted:#8a8a8a;
  --soft:#f3f0f0;
  --pale:#e2e2e2;
  --footer:#1c1c1c;
  --white:#fff;
}
*{margin:0;padding:0;box-sizing:border-box}
html,body{width:1200px;height:4724px;overflow:hidden;background:var(--white)}
body{font-family:"Open Sans",Arial,sans-serif;color:var(--body)}
.page{position:relative;width:1200px;height:4724px;overflow:hidden}
.abs{position:absolute}
h1,h2,h3,h4,.brand-name,.btn,.nav a{font-family:"Poppins",Arial,sans-serif}
.btn{position:absolute;background:var(--accent);color:var(--white);font-weight:700;font-size:14px;display:flex;align-items:center;justify-content:center;letter-spacing:.5px;text-transform:uppercase;box-shadow:0 4px 10px rgba(0,0,0,.15)}
.section-title{position:absolute;left:0;width:1200px;text-align:center;color:var(--ink);font-size:30px;font-weight:700;line-height:40px}
.title-rule{position:absolute;left:570px;width:60px;height:2px;background:#c8c8c8}

/* header */
.brand{position:absolute;display:flex;flex-direction:column;align-items:center}
.brand-mark{width:34px;height:34px;background:var(--accent);margin-bottom:12px}
.brand-name{font-weight:800;font-size:26px;color:var(--ink);letter-spacing:.3px}
.call{left:628px;top:32px;display:flex;align-items:center;gap:12px}
.call small{display:block;font-size:11px;font-weight:700;color:var(--ink);line-height:13px}
.call strong{display:block;font-family:"Poppins",Arial,sans-serif;font-size:22px;font-weight:700;color:var(--ink);line-height:26px}
.follow{left:876px;top:40px;display:flex;align-items:center;gap:6px;font-size:11px;font-weight:700;color:var(--ink)}
.dot-social{width:24px;height:24px;border-radius:50%;background:#1f4f9e;display:inline-block}
.nav{left:500px;top:104px;display:flex;gap:34px}
.nav a{font-size:13px;font-weight:700;color:var(--ink);text-decoration:none;padding-bottom:6px}
.nav a.active{color:var(--accent);border-bottom:2px solid var(--accent)}

/* hero */
.hero{left:0;top:145px;width:1200px;height:580px;background:linear-gradient(180deg,#4f8bc7 0%,#8fb7da 45%,#c9c6b9 70%,#3f5a2c 100%)}
.hero h1{position:absolute;left:145px;top:120px;color:var(--white);font-size:58px;font-weight:800;line-height:62px;text-shadow:0 2px 6px rgba(0,0,0,.3)}
.slider-dots{left:548px;top:516px;display:flex;gap:10px}
.slider-dots span{width:10px;height:10px;border-radius:50%;background:var(--white)}
.slider-dots span.on{background:var(--accent)}

/* services */
.services-photo{left:142px;top:787px;width:440px;height:535px;background:linear-gradient(180deg,#b9c6d4 0%,#7e6f66 55%,#5a3f36 100%);box-shadow:0 6px 18px rgba(0,0,0,.25)}
.services-card{left:580px;top:820px;width:480px;height:500px}
.services-card h2{position:absolute;left:50px;top:40px;font-size:30px;font-weight:700;color:var(--ink)}
.services-card p{position:absolute;left:50px;width:400px;font-size:14px;line-height:20px}
.service-list{position:absolute;left:50px;top:193px;list-style:none}
.service-list li{font-family:"Poppins",Arial,sans-serif;font-size:14px;font-weight:600;color:var(--ink);line-height:25px;padding-left:16px;position:relative}
.service-list li:before{content:"";position:absolute;left:0;top:8px;border-left:6px solid var(--ink);border-top:4px solid transparent;border-bottom:4px solid transparent}

/* why choose */
.why{left:0;top:1400px;width:1200px;height:640px}
.why-art{left:420px;top:1570px;width:360px;height:360px;background:linear-gradient(180deg,rgba(200,200,200,.25),rgba(200,200,200,.5))}
.feature{position:absolute;width:250px}
.feature h3{font-size:16px;font-weight:700;color:var(--ink);line-height:22px;margin-bottom:4px}
.feature p{font-size:13px;line-height:17px}
.feature.right{text-align:left}
.feature-icon{position:absolute;width:66px;height:66px;border-radius:50%;background:var(--navy);display:flex;align-items:center;justify-content:center}

/* process */
.step{position:absolute;width:300px;text-align:center}
.step svg{display:block;margin:0 auto}
.step h3{font-size:16px;font-weight:700;color:var(--ink);margin-top:44px}
.step p{font-size:13px;line-height:17px;margin:12px auto 0;width:260px}
.step .num{font-family:"Poppins",Arial,sans-serif;font-size:40px;font-weight:800;color:#e9e9e9;margin-top:14px}

/* projects */
.projects{left:0;top:2504px;width:1200px;height:819px;background:#f4f4f4}
.project{position:absolute;width:299px;height:258px}
.project span{position:absolute;left:0;right:0;bottom:0;height:80px;background:linear-gradient(180deg,rgba(0,0,0,0),rgba(0,0,0,.75));color:var(--white);font-family:"Poppins",Arial,sans-serif;font-weight:700;font-size:17px;display:flex;align-items:flex-end;padding:0 0 16px 24px}

/* blog */
.blog-card{position:absolute;width:258px;height:341px;background:var(--white);box-shadow:0 4px 16px rgba(0,0,0,.18)}
.blog-card .thumb{height:185px;border-bottom:5px solid var(--accent)}
.blog-card h4{font-size:14px;font-weight:700;color:var(--ink);line-height:18px;margin:16px 20px 8px 38px}
.blog-card p{font-size:11px;line-height:14px;color:var(--muted);margin:0 20px 0 38px}
.blog-card .btn{right:12px;bottom:14px;width:76px;height:22px;font-size:10px}
.blog-card .edge{position:absolute;left:0;top:190px;width:6px;height:151px;background:var(--accent)}
.arrow{position:absolute;top:3650px;font-size:34px;color:#9a9a9a;font-family:"Poppins",Arial,sans-serif}

/* cta */
.cta{left:0;top:3906px;width:1200px;height:432px;background:linear-gradient(90deg,#c7a88f 0%,#d9b9a8 40%,#b8a9c1 70%,#6b6f98 100%)}
.cta h2{position:absolute;left:740px;top:80px;width:400px;font-size:30px;font-weight:700;line-height:36px;color:var(--ink)}

/* footer */
.footer{left:0;top:4338px;width:1200px;height:386px;background:var(--footer);color:#cfcfcf}
.footer h4{position:absolute;top:55px;font-size:12px;font-weight:700;color:var(--white);letter-spacing:.5px}
.footer .brand-name{color:var(--white)}
.contact-item{position:absolute;left:488px;display:flex;gap:12px;font-size:11px;line-height:15px;align-items:flex-start}
.menu-list{position:absolute;left:734px;top:88px;list-style:none;font-size:11px;line-height:15px}
.connect{position:absolute;left:930px;display:flex;align-items:center;gap:12px;font-size:11px}
.connect .dot-social{width:22px;height:22px}
.copyright{position:absolute;left:0;top:322px;width:1200px;text-align:center;font-size:11px;color:#9a9a9a}
</style>
</head>
<body>
<div class="page">

  <!-- header -->
  <header>
    <div class="brand" style="left:133px;top:18px;width:300px">
      <span class="brand-mark"></span>
      <span class="brand-name">KPL CONSTRUCTION</span>
    </div>
    <div class="call abs">
      <svg width="24" height="24" viewBox="0 0 24 24"><path fill="#1d1d1d" d="M6.6 10.8a15.1 15.1 0 0 0 6.6 6.6l2.2-2.2c.3-.3.7-.4 1-.2 1.1.4 2.3.6 3.6.6.6 0 1 .4 1 1V20c0 .6-.4 1-1 1A17 17 0 0 1 3 4c0-.6.4-1 1-1h3.5c.6 0 1 .4 1 1 0 1.3.2 2.5.6 3.6.1.3 0 .7-.2 1z"/></svg>
      <div><small>CALL US NOW</small><strong>555.014.7720</strong></div>
    </div>
    <div class="follow abs">FOLLOW US &nbsp;<span class="dot-social"></span><span class="dot-social"></span><span class="dot-social"></span></div>
    <nav class="nav abs">
      <a class="active">HOME</a><a>ABOUT US</a><a>PROJECTS</a><a>SERVICES</a><a>TESTIMONIALS</a><a>CONTACT US</a>
    </nav>
  </header>

  <!-- hero -->
  <section class="hero abs" role="img" aria-label="Photo of a modern white lodge with palm trees at dusk">
    <h1>LODGES<br>CONSTRUCTION</h1>
    <div class="btn" style="left:150px;top:258px;width:160px;height:48px">Read More</div>
    <div class="slider-dots abs" style="left:548px;top:516px"><span></span><span></span><span class="on"></span><span></span><span></span></div>
  </section>

  <!-- services -->
  <div class="services-photo abs" role="img" aria-label="Photo of a tall residential tower beside a domed building"></div>
  <section class="services-card abs">
    <h2>Our Services</h2>
    <p style="top:105px">Lorem ipsum dolor sit amet, consectetur adipiscing elit, sed do eiusmod tempor incididunt ut labore et dolore magna aliqua. Ut enim ad minim veniam.</p>
    <ul class="service-list">
      <li>Stonemasonry</li><li>Joinery</li><li>Carpentry</li><li>Leadwork</li><li>Stone Conservation</li>
    </ul>
    <p style="top:352px">Labore et dolore magna aliqua. Ut enim ad minim veniam, quis nostrud exercitation ullamco laboris.</p>
    <div class="btn" style="left:53px;top:420px;width:128px;height:40px;font-size:13px">Read More</div>
  </section>

  <!-- why choose us -->
  <section class="why abs">
    <svg class="abs" style="left:0;top:0" width="1200" height="640" viewBox="0 0 1200 640">
      <path d="M0 0H1200V640H1200C1050 560 850 512 600 512S150 560 0 640Z" fill="#f3f0f0"/>
    </svg>
  </section>
  <div class="why-art abs" role="img" aria-label="Faint line drawing of an office building"></div>
  <h2 class="section-title" style="top:1455px">Why Choose us</h2>
  <div class="title-rule" style="top:1508px"></div>

  <div class="feature-icon" style="left:124px;top:1580px"><svg width="30" height="30" viewBox="0 0 30 30"><circle cx="15" cy="15" r="12" fill="none" stroke="#fff" stroke-width="2.5"/><path d="M8 15c4-6 10-6 14 0-4 5-10 5-14 0z" fill="#fff"/></svg></div>
  <div class="feature" style="left:220px;top:1572px"><h3>Sustainable Living</h3><p>Lorem ipsum dolor sit amet, consectetur adipiscing elit, sed do eiusmod tempor incididunt cillum dolore eu fugiat nulla pariatur.</p></div>

  <div class="feature-icon" style="left:1030px;top:1580px"><svg width="26" height="30" viewBox="0 0 26 30"><rect x="2" y="1" width="22" height="28" rx="2" fill="none" stroke="#fff" stroke-width="2.5"/><rect x="6" y="5" width="14" height="6" fill="#fff"/><g fill="#fff"><rect x="6" y="14" width="4" height="3"/><rect x="11" y="14" width="4" height="3"/><rect x="16" y="14" width="4" height="3"/><rect x="6" y="20" width="4" height="3"/><rect x="11" y="20" width="4" height="3"/><rect x="16" y="20" width="4" height="3"/></g></svg></div>
  <div class="feature right" style="left:815px;top:1572px"><h3>Cost Estimates</h3><p>Lorem ipsum dolor sit amet, consectetur adipiscing elit, sed do eiusmod tempor incididunt cillum dolore eu fugiat nulla pariatur.</p></div>

  <div class="feature-icon" style="left:124px;top:1758px"><svg width="32" height="28" viewBox="0 0 32 28"><circle cx="16" cy="8" r="5" fill="#fff"/><circle cx="7" cy="11" r="3.5" fill="#fff"/><circle cx="25" cy="11" r="3.5" fill="#fff"/><path d="M7 26c0-7 4-11 9-11s9 4 9 11zM0 24c0-5 3-8 7-8v8zM32 24c0-5-3-8-7-8v8z" fill="#fff"/></svg></div>
  <div class="feature" style="left:220px;top:1750px"><h3>Professional Team</h3><p>Lorem ipsum dolor sit amet, consectetur adipiscing elit, sed do eiusmod tempor incididunt cillum dolore eu fugiat nulla pariatur.</p></div>

  <div class="feature-icon" style="left:1030px;top:1758px"><svg width="30" height="28" viewBox="0 0 30 28"><rect x="1" y="1" width="20" height="15" rx="2" fill="none" stroke="#fff" stroke-width="2.5"/><rect x="9" y="9" width="20" height="15" rx="2" fill="#fff"/><path d="M14 24v4l5-4z" fill="#fff"/></svg></div>
  <div class="feature right" style="left:815px;top:1750px"><h3>Communication</h3><p>Lorem ipsum dolor sit amet, consectetur adipiscing elit, sed do eiusmod tempor incididunt cillum dolore eu fugiat nulla pariatur.</p></div>

  <!-- working process -->
  <h2 class="section-title" style="top:1985px">Our Working Process<br>in 3 steps</h2>
  <div class="title-rule" style="top:2080px"></div>

  <div class="step" style="left:120px;top:2155px">
    <svg width="84" height="84" viewBox="0 0 84 84"><rect x="4" y="4" width="76" height="76" fill="none" stroke="#0f2b5b" stroke-width="5"/><rect x="14" y="14" width="56" height="56" fill="none" stroke="#0f2b5b" stroke-width="3"/><path d="M14 42H42V14M42 56H70M28 42V70" stroke="#0f2b5b" stroke-width="3" fill="none"/></svg>
    <h3>Planning &amp; Strategy</h3>
    <p>Sed ut perspiciatis unde omnis iste natus error sit voluptatem accusa ntium doloremque laudantium, totam rem aperiam, eaque ipsa.</p>
    <div class="num">01</div>
  </div>
  <div class="step" style="left:450px;top:2155px">
    <svg width="84" height="84" viewBox="0 0 84 84"><g transform="rotate(-45 42 42)"><rect x="6" y="33" width="72" height="18" fill="#0f2b5b"/><path d="M18 33v7M28 33v10M38 33v7M48 33v10M58 33v7" stroke="#fff" stroke-width="2"/></g><g transform="rotate(45 42 42)"><rect x="10" y="35" width="58" height="14" fill="#0f2b5b"/><path d="M68 35l12 7-12 7z" fill="#0f2b5b"/></g></svg>
    <h3>Design &amp; Develop</h3>
    <p>Sed ut perspiciatis unde omnis iste natus error sit voluptatem accusa ntium doloremque laudantium, totam rem aperiam, eaque ipsa.</p>
    <div class="num">02</div>
  </div>
  <div class="step" style="left:775px;top:2155px">
    <svg width="84" height="84" viewBox="0 0 84 84"><rect x="26" y="8" width="32" height="72" fill="#0f2b5b"/><rect x="6" y="36" width="20" height="44" fill="#0f2b5b"/><rect x="58" y="28" width="20" height="52" fill="#0f2b5b"/><g fill="#fff"><rect x="32" y="16" width="6" height="6"/><rect x="46" y="16" width="6" height="6"/><rect x="32" y="30" width="6" height="6"/><rect x="46" y="30" width="6" height="6"/><rect x="32" y="44" width="6" height="6"/><rect x="46" y="44" width="6" height="6"/><rect x="12" y="46" width="8" height="4"/><rect x="12" y="58" width="8" height="4"/><rect x="64" y="38" width="8" height="4"/><rect x="64" y="50" width="8" height="4"/><rect x="37" y="64" width="10" height="16"/></g></svg>
    <h3>Complete &amp; Deliver</h3>
    <p>Sed ut perspiciatis unde omnis iste natus error sit voluptatem accusa ntium doloremque laudantium, totam rem aperiam, eaque ipsa.</p>
    <div class="num">03</div>
  </div>

  <!-- projects -->
  <section class="projects abs">
    <h2 class="section-title" style="top:51px">Our Projects</h2>
    <div class="title-rule" style="top:104px"></div>
    <div class="project" style="left:142px;top:151px;background:linear-gradient(180deg,#1c2a44,#5a4630 70%,#2b2620)" role="img" aria-label="Photo of a modern lodge lit at night"><span>LOREM IPSUM</span></div>
    <div class="project" style="left:450px;top:151px;background:linear-gradient(180deg,#a8bccf,#6e5440 60%,#3e3326)" role="img" aria-label="Photo of a timber mountain lodge"><span>LOREM IPSUM</span></div>
    <div class="project" style="left:757px;top:151px;background:linear-gradient(180deg,#2c1a20,#8a3a2a 50%,#3a1c16)" role="img" aria-label="Photo of a brick hotel at dusk"><span>LOREM IPSUM</span></div>
    <div class="project" style="left:142px;top:419px;background:linear-gradient(180deg,#8fb0d3,#b9a98f 55%,#4e4a40)" role="img" aria-label="Photo of a curved resort hotel"><span>LOREM IPSUM</span></div>
    <div class="project" style="left:450px;top:419px;background:linear-gradient(180deg,#7ea6d0,#c7a17a 55%,#5a4634)" role="img" aria-label="Photo of a sandstone apartment block"><span>LOREM IPSUM</span></div>
    <div class="project" style="left:757px;top:419px;background:linear-gradient(180deg,#2d56a8,#5d7fb8 50%,#2c3442)" role="img" aria-label="Photo of a glass residential building"><span>LOREM IPSUM</span></div>
    <div class="btn" style="left:507px;top:3225px;width:186px;height:40px;font-size:13px;top:721px">View All Projects</div>
  </section>

  <!-- blog -->
  <h2 class="section-title" style="top:3385px">Latest Blog</h2>
  <div class="title-rule" style="top:3438px"></div>
  <div class="arrow" style="left:95px">&#8249;</div>
  <div class="arrow" style="left:1090px">&#8250;</div>

  <article class="blog-card" style="left:167px;top:3496px">
    <div class="thumb" role="img" aria-label="Photo of a hotel tower at dusk" style="background:linear-gradient(180deg,#2d4f8a,#b5552d 70%,#3a2a22)"></div>
    <span class="edge"></span>
    <h4>Lorem Ipsum is simply dummy text of the printing</h4>
    <p>Sed ut perspiciatis unde omnis iste natus error sit voluptatem accusantium.</p>
    <div class="btn">Read More</div>
  </article>
  <article class="blog-card" style="left:472px;top:3496px">
    <div class="thumb" role="img" aria-label="Photo of a lit glass tower at night" style="background:linear-gradient(180deg,#1a2f7a,#3a5fb8 60%,#1b2040)"></div>
    <span class="edge"></span>
    <h4>Lorem Ipsum is simply dummy text of the printing</h4>
    <p>Sed ut perspiciatis unde omnis iste natus error sit voluptatem accusantium.</p>
    <div class="btn">Read More</div>
  </article>
  <article class="blog-card" style="left:778px;top:3496px">
    <div class="thumb" role="img" aria-label="Photo of a classic stone hotel at dusk" style="background:linear-gradient(180deg,#1e3468,#c79b5a 60%,#3b2c1e)"></div>
    <span class="edge"></span>
    <h4>Lorem Ipsum is simply dummy text of the printing</h4>
    <p>Sed ut perspiciatis unde omnis iste natus error sit voluptatem accusantium.</p>
    <div class="btn">Read More</div>
  </article>

  <!-- call to action -->
  <section class="cta abs" role="img" aria-label="Photo of a seaside resort building at sunset">
    <h2>Lorem Ipsum is simply dummy text of the printing</h2>
    <div class="btn" style="left:745px;top:234px;width:165px;height:44px">Contact Us</div>
  </section>

  <!-- footer -->
  <footer class="footer abs">
    <div class="brand" style="left:133px;top:90px;width:300px">
      <span class="brand-mark"></span>
      <span class="brand-name">KPL CONSTRUCTION</span>
    </div>

    <h4 style="left:488px">CONTACT US</h4>
    <div class="contact-item" style="top:92px"><svg width="12" height="14" viewBox="0 0 12 14"><path d="M6 0a5 5 0 0 1 5 5c0 4-5 9-5 9S1 9 1 5a5 5 0 0 1 5-5z" fill="#fff"/><circle cx="6" cy="5" r="2" fill="#1c1c1c"/></svg><span>12 Acacia Lane<br>Maun 0267</span></div>
    <div class="contact-item" style="top:140px"><svg width="12" height="12" viewBox="0 0 24 24"><path fill="#fff" d="M6.6 10.8a15.1 15.1 0 0 0 6.6 6.6l2.2-2.2c.3-.3.7-.4 1-.2 1.1.4 2.3.6 3.6.6.6 0 1 .4 1 1V20c0 .6-.4 1-1 1A17 17 0 0 1 3 4c0-.6.4-1 1-1h3.5c.6 0 1 .4 1 1 0 1.3.2 2.5.6 3.6.1.3 0 .7-.2 1z"/></svg><span>555.014.7720</span></div>
    <div class="contact-item" style="top:174px"><svg width="12" height="10" viewBox="0 0 12 10"><rect width="12" height="10" fill="#fff"/><path d="M0 0l6 5 6-5" stroke="#1c1c1c" fill="none"/></svg><span>info@kpl.construction</span></div>

    <h4 style="left:734px">MENU</h4>
    <ul class="menu-list"><li>HOME</li><li>ABOUT US</li><li>PROJECTS</li><li>SERVICES</li><li>TESTIMONIALS</li><li>CONTACT US</li></ul>

    <h4 style="left:930px">CONNECT WITH US</h4>
    <div class="connect" style="top:88px"><span class="dot-social"></span>Facepage</div>
    <div class="connect" style="top:130px"><span class="dot-social"></span>Chirper</div>
    <div class="connect" style="top:172px"><span class="dot-social"></span>WorkLink</div>

    <div class="abs" style="left:0;top:292px;width:1200px;height:1px;background:#333"></div>
    <p class="copyright">Copyright &copy; 2019 All Rights Reserved</p>
  </footer>

</div>
</body>
</html>
```